Counseling Practice Business Card

I need a professional looking business card incorporating my new logo that was just completed. Card needs to incorporate my name and title, description of my specialty, my address, my phone number, my fax number, my email and my website URL. I need to be able to choose design on/with different paper colors and textures.
I do not have a lot of business card ideas so I am open to anything but I want bold,sharp, clear card without additional designs other than my logo (see attached file info). I am open to different color backgrounds or paper colors including black. I do not like traditional brackets around area codes in phone number or dashes between numbers in phone number. Am open to other ways of presenting including periods between numbers as appropriate. I do not know enough to know what I like yet but I want card to coordinate and work together with my logo. My practice emphasizes natural mental health interventions so any use of color (with background paper color or the blue and green in my logo) that elicits nature is nice. In addition to black, any natural brown or wood looking background might be desirable also. Most of the offerings so far look very similar and boring.

Target Market(s)

Potential therapy clients and other professionals

Contact Information for Business Card

Card information:
Gerald M. Whitcombe, Ph.D.
Licensed Clinical Psychologist
Integrative Health Coach
4812 Marlowe Ridge Blvd SE
Suite 310
Lakemont, GA 30248
(770) 415-2983 phone
(770) 581-4096 fax
drgeraldwhitcombe@quillmarsh.net
brightfernwellness.net

Font styles to use
Serif
Sans Serif
Other font styles liked:
• anything that you think looks crisp, clear and easily readable

Requirements
Must have
• Any color used should coordinate with my logo design (see attached files).
• Card should be printed horizontally so top and bottom are longest sides of rectangle.
• Background color or paper color should complement and highlight logo. Do not like a white background. black, grey, brown or any color my logo would blend well with.
Nice to have
• I would like designer to utilize color to highlight letters/name or phone-fax-web symbols.
• Bottom edge of card could be highlighted if appropriate to an idea.
Should not have
• I would NOT want the card to have a pure white background at all.
• No clear cards.
• Cards should be oriented with long sides on bottom and top, NOT sides. DO NOT LIKE THIS THIN TALL ORIENTATION.

```html
<!DOCTYPE html>
<html lang="en">
<head>
<meta charset="utf-8">
<title>Brightfern Wellness – Business Card</title>
<link href="https://fonts.googleapis.com/css2?family=Roboto:wght@400;500;700&display=swap" rel="stylesheet">
<style>
  :root {
    --backdrop: #d3d8d8;
    --paper: #f3f3ef;
    --brand-blue: #2a6fc2;
    --brand-green: #1f6a2e;
    --ink: #3a3a3a;
    --ink-soft: #555;
    --on-blue: #ffffff;
  }
  * { box-sizing: border-box; margin: 0; padding: 0; }
  html, body {
    width: 1200px; height: 930px; overflow: hidden;
    background: var(--backdrop);
    font-family: "Roboto", Arial, sans-serif;
  }
  .canvas { position: relative; width: 1200px; height: 930px; }
  .card {
    position: absolute; left: 250px; width: 700px; height: 400px;
    overflow: hidden;
    box-shadow: 0 6px 18px rgba(0,0,0,.18);
  }
  .card--front { top: 50px; background: var(--paper); }
  .card--back  { top: 480px; background: var(--brand-blue); }

  /* front */
  .identity { position: absolute; left: 44px; top: 40px; }
  .identity__name { color: var(--brand-blue); font-weight: 700; font-size: 27px; letter-spacing: .2px; }
  .identity__title { color: var(--ink-soft); font-size: 19px; line-height: 1.25; margin-top: 4px; }
  .divider { position: absolute; background: var(--brand-blue); }
  .divider--top { top: 148px; left: 44px; width: 326px; height: 2px; }
  .divider--bottom { top: 262px; left: 44px; right: 44px; height: 1.5px; }
  .contact { position: absolute; left: 44px; top: 164px; list-style: none; }
  .contact__item {
    display: flex; align-items: center; gap: 10px;
    color: var(--ink); font-size: 17px; line-height: 23px;
  }
  .contact__icon { width: 13px; height: 13px; fill: var(--brand-blue); flex: none; }
  .contact__icon--line { fill: none; stroke: var(--brand-blue); stroke-width: 1.6; }
  .contact__web { color: var(--brand-blue); }
  .brand-mark {
    position: absolute; right: 44px; top: 100px;
    color: var(--brand-blue); font-weight: 700; font-size: 34px; line-height: 1.1;
    text-align: right;
  }
  .address {
    position: absolute; right: 44px; top: 290px; text-align: right;
    color: var(--ink); font-size: 17px; line-height: 23px; font-style: normal;
  }
  .edge-band { position: absolute; left: 0; bottom: 0; width: 700px; height: 48px; }

  /* back */
  .back-brand {
    position: absolute; inset: 0; display: flex; align-items: center; justify-content: center;
    color: var(--on-blue); font-weight: 700; font-size: 58px; letter-spacing: .5px;
  }
  .back-web {
    position: absolute; left: 0; right: 0; bottom: 34px; text-align: center;
    color: var(--on-blue); font-size: 17px;
  }
</style>
</head>
<body>
<main class="canvas">
  <section class="card card--front">
    <div class="identity">
      <h1 class="identity__name">Gerald M. Whitcombe, Ph.D.</h1>
      <p class="identity__title">Licensed Clinical Psychologist<br>Integrative Health Coach</p>
    </div>
    <div class="divider divider--top"></div>
    <ul class="contact">
      <li class="contact__item">
        <svg class="contact__icon" viewBox="0 0 16 16"><path d="M3.5 1l2.5 3-1.5 2c1 2 3 4 5 5l2-1.5 3 2.5-1.5 2.5C7 14.5 1.5 9 1 2.5z"/></svg>
        (770) 415-2983
      </li>
      <li class="contact__item">
        <svg class="contact__icon" viewBox="0 0 16 16"><rect x="4" y="1" width="8" height="5"/><rect x="1" y="6" width="14" height="7" rx="1"/><rect x="4" y="11" width="8" height="4" fill="#f3f3ef"/></svg>
        (770) 581-4096
      </li>
      <li class="contact__item">
        <svg class="contact__icon contact__icon--line" viewBox="0 0 16 16"><path d="M1 3h14v10H1z M1 3l7 6 7-6"/></svg>
        drgeraldwhitcombe@quillmarsh.net
      </li>
      <li class="contact__item">
        <svg class="contact__icon" viewBox="0 0 16 16"><circle cx="8" cy="8" r="7"/><path d="M1 8h14M8 1c-3 3-3 11 0 14M8 1c3 3 3 11 0 14" stroke="#f3f3ef" stroke-width="1" fill="none"/></svg>
        <span>www.<span class="contact__web">brightfernwellness</span>.net</span>
      </li>
    </ul>
    <div class="brand-mark">Brightfern<br>Wellness</div>
    <div class="divider divider--bottom"></div>
    <address class="address">
      4812 Marlowe Ridge Blvd SE<br>Suite 310 Lakemont, GA 30248
    </address>
    <svg class="edge-band" viewBox="0 0 700 48" preserveAspectRatio="none">
      <rect x="0" y="38" width="360" height="10" fill="var(--brand-green)"/>
      <polygon points="330,48 380,0 700,0 700,48" fill="var(--brand-blue)"/>
    </svg>
  </section>

  <section class="card card--back">
    <div class="back-brand">Brightfern Wellness</div>
    <p class="back-web">www.brightfernwellness.net</p>
  </section>
</main>
</body>
</html>
```